Therapy Dog Business need a brochure

I need a brochure designed for my Canine Assisted Therapy business in Victoria Australia. I have a logo already and info and photos to upload.
Best as white background and using the colours from the logo please
Updates

Hi Everyone,
I am sorry to have to revise the brief. I have added three new photos I was unable to add due to the size. I have had to wait for my photographer to change the size to add them today. I have been really inspired by all the work you have done so far. Thank you.
Could you please add the following on the brochure. (Under the individual dogs photo)
1. Pepper is the white dog. Please add the following under her picture. Pepper is one of the first Court Dogs in Australia. Working in Victoria, she has worked in the following Courts. The Halbrook Inquest Court, The Brindle Hearing Court in Collingwood, and the Fenwick Court in Melbourne CBD. Her ability to use her intuition for clients is inspiring. Please contact us for potential use in Courts. Pepper has worked at the Marlow Constabulary College, and at TALON at Mar Con. She is a stunning dog!
2. Barnaby is the golden dog. Barnaby is Peppers son, and had her instinct of intuition of who needs his help. Barnaby has an incredible soft approach as does his mother Pepper. He is incredibly safe with young children, and yet has a playful nature for adolescents and adults alike. He is soft and caring, and like his mother will go to those who need him most. Barnaby like his mother has worked at Marlow Constabulary, his time at MC included the Marlow Constabulary Directorate (MCD) Both he and his mother have very impressive CV'S!
3. Tansy the black dog. Tansy is my Therapy and Assistance dog "trainer" she is safe and stable with all the dogs and people I train for Therapy Dog Training and Assistance Dog Training. She has also been with me on my journey as a Counsellor and I have been able to work alongside her and Pepper for Counselling sessions.
She is soft, caring, and also intuitive. I am incredibly grateful for her help, as well as Pepper and Barnaby.
ALSO I am so sorry to add this but could you also add the following: Maybe in dot point?
Court Dog Availability
Therapy Dog Visits - Lawyers - Courts - Child Protection
Police Station / Ambulance Station / Fire Station - Visits
Private Therapy Dog Sessions
website and email confirmation coming soon. Thank you

Target Market(s)

First Responders

Requirements
Must have
• All the photos provided.
Should not have
• Generic photos

```html
<!DOCTYPE html>
<html lang="en">
<head>
<meta charset="utf-8">
<title>Kindred Paws – Canine Assisted Therapy Brochure</title>
<link href="https://fonts.googleapis.com/css2?family=Lexend:wght@300;400;500;600&display=swap" rel="stylesheet">
<style>
  :root{
    --paper:#ffffff;
    --maroon:#4a1418;
    --maroon-deep:#5e1b1e;
    --heading:#6a1d1f;
    --orange:#e8874a;
    --orange-soft:#f0a35e;
    --pink:#e07a76;
    --ink:#333333;
    --ring-grey:#ececec;
    --footer-grey:#ededed;
  }
  *{box-sizing:border-box;margin:0;padding:0}
  html,body{width:1200px;height:900px;overflow:hidden;background:var(--paper)}
  body{font-family:"Lexend",sans-serif;color:var(--ink)}
  .brochure{position:absolute;left:0;top:0;width:1200px;height:900px;background:var(--paper);overflow:hidden}
  .abs{position:absolute}

  .hero-photo{left:0;top:28px;width:622px;height:230px}

  .intro-title{left:646px;top:44px;font-size:28px;font-weight:600;color:var(--heading);white-space:nowrap}
  .intro-title .accent{color:var(--orange)}
  .intro-body{left:650px;top:86px;font-size:15.8px;font-weight:300;line-height:21.2px;color:var(--ink);white-space:nowrap}

  .pill{height:42px;background:var(--maroon);border-radius:21px;color:#fff;font-size:23.5px;font-weight:500;
        display:flex;align-items:center;justify-content:center;white-space:nowrap}
  .pill .accent{color:var(--orange-soft)}
  .pill::after{content:"";position:absolute;left:50%;bottom:-9px;margin-left:-10px;border-left:10px solid transparent;border-right:10px solid transparent;border-top:10px solid var(--maroon)}
  .pill-benefits{left:62px;top:288px;width:493px}
  .pill-why{left:650px;top:288px;width:508px}

  .hub{left:0;top:0;width:1200px;height:900px;pointer-events:none}

  .point h3{font-size:18.5px;font-weight:500;color:var(--heading);white-space:nowrap;margin-bottom:7px}
  .point p{font-size:12px;font-weight:300;line-height:15.4px;color:var(--ink);white-space:nowrap}
  .point.left{text-align:right}
  .p-emotional{right:794px;top:352px}
  .p-stress{right:855px;top:495px}
  .p-emotional-2{right:788px;top:646px}
  .p-emotional-2 h3{margin-right:12px}
  .p-proven{left:795px;top:352px}
  .p-gentle{left:858px;top:495px}
  .p-gentle h3{margin-left:8px}
  .p-safe{left:800px;top:646px}
  .p-safe h3{margin-left:14px}
  .p-safe p{font-size:11.5px}

  .dog-photo{left:1018px;top:592px;width:182px;height:200px}

  .footer{left:0;top:792px;width:1200px;height:108px}
  .join{left:29px;top:812px;font-size:25px;font-weight:600;line-height:32px;color:var(--maroon);white-space:nowrap}
  .footer-copy{left:289px;top:810px;font-size:13.6px;font-weight:400;line-height:17.8px;color:#fff;white-space:nowrap}
  .contacts{left:910px;top:806px;list-style:none}
  .contacts li{display:flex;align-items:center;gap:12px;height:28px;font-size:17px;font-weight:400;color:#222;white-space:nowrap}
  .contacts svg{flex:none}
</style>
</head>
<body>
<main class="brochure">

  <svg class="abs hero-photo" viewBox="0 0 622 230" role="img" aria-label="Photo of two golden Labradors and a black Labrador resting on a blue blanket-covered couch against a brick wall">
    <defs>
      <linearGradient id="heroFill" x1="0" y1="0" x2="0" y2="1">
        <stop offset="0" stop-color="#b47a5c"/>
        <stop offset="0.35" stop-color="#8b96cc"/>
        <stop offset="0.75" stop-color="#c9a577"/>
        <stop offset="1" stop-color="#7d8ac4"/>
      </linearGradient>
      <linearGradient id="arcFill" x1="0" y1="0" x2="0" y2="1">
        <stop offset="0" stop-color="#d9653d"/>
        <stop offset="1" stop-color="#f0a05a"/>
      </linearGradient>
    </defs>
    <path d="M500 0 A120 115 0 0 1 622 115 A120 115 0 0 1 500 230 L500 225 A112 110 0 0 0 610 115 A112 110 0 0 0 500 5 Z" fill="url(#arcFill)"/>
    <path d="M0 2 H492 A114 112 0 0 1 606 114 A114 112 0 0 1 492 226 H0 Z" fill="url(#heroFill)"/>
  </svg>

  <h1 class="abs intro-title">What is <span class="accent">Canine Assisted Therapy?</span></h1>
  <p class="abs intro-body">Canine Assisted Therapy (CAT) is a unique form of therapy that<br>integrates trained therapy dogs into the healing process.&nbsp; By<br>working alongside licensed therapists, these compassionate<br>and well-trained dogs help support individuals in overcoming<br>emotional, physical, and psychological challenges.&nbsp; This<br>innovative approach promotes healing, reduces stress, and<br>enhances overall well-being.</p>

  <h2 class="abs pill pill-benefits"><span><span class="accent">Benefits</span> of Canine Assisted Therapy</span></h2>
  <h2 class="abs pill pill-why"><span><span class="accent">Why Choose</span> Canine Assisted Therapy?</span></h2>

  <svg class="abs hub" viewBox="0 0 1200 900">
    <defs>
      <linearGradient id="badge" x1="0" y1="0" x2="0" y2="1">
        <stop offset="0" stop-color="#d8743f"/>
        <stop offset="1" stop-color="#7a2419"/>
      </linearGradient>
    </defs>
    <circle cx="602" cy="545" r="194" fill="none" stroke="#8a2a24" stroke-width="1.3"/>
    <circle cx="602" cy="545" r="148" fill="var(--ring-grey)"/>
    <circle cx="602" cy="545" r="110" fill="#fff" stroke="var(--maroon)" stroke-width="3"/>
    <text x="602" y="552" text-anchor="middle" font-family="Lexend, sans-serif" font-size="20" font-weight="600" fill="#4a1418">Kindred Paws</text>
    <g>
      <circle cx="468" cy="395" r="40" fill="url(#badge)" stroke="#5a1a1a" stroke-width="3"/>
      <circle cx="397" cy="540" r="40" fill="url(#badge)" stroke="#5a1a1a" stroke-width="3"/>
      <circle cx="460" cy="690" r="40" fill="url(#badge)" stroke="#5a1a1a" stroke-width="3"/>
      <circle cx="736" cy="395" r="40" fill="url(#badge)" stroke="#5a1a1a" stroke-width="3"/>
      <circle cx="808" cy="540" r="40" fill="url(#badge)" stroke="#5a1a1a" stroke-width="3"/>
      <circle cx="744" cy="690" r="40" fill="url(#badge)" stroke="#5a1a1a" stroke-width="3"/>
    </g>
    <g fill="none" stroke="#fff" stroke-width="1.6" stroke-linejoin="round" stroke-linecap="round">
      <path d="M719 381 h34 a6 6 0 0 1 6 6 v18 a6 6 0 0 1 -6 6 h-14 l-8 8 v-8 h-12 a6 6 0 0 1 -6 -6 v-18 a6 6 0 0 1 6 -6 z"/>
      <path d="M723 390 h26 M723 396 h26 M723 402 h18"/>
      <path d="M808 558 c-10 -8 -17 -14 -17 -21 a8 8 0 0 1 17 -3 a8 8 0 0 1 17 3 c0 7 -7 13 -17 21 z"/>
      <path d="M744 672 l16 6 v12 c0 10 -7 17 -16 21 c-9 -4 -16 -11 -16 -21 v-12 z"/>
      <path d="M453 681 h8 v-8 h8 v8 h8 v8 h-8 v8 h-8 v-8 h-8 z"/>
    </g>
  </svg>

  <section class="abs point left p-emotional">
    <h3>Emotional Support and Comfort</h3>
    <p>Therapy dogs provide immediate emotional support,<br>offering comfort and companionship during therapy<br>sessions.&nbsp; Their calming presence helps reduce feelings<br>of anxiety, stress, and depression, and grief, creating a<br>safe and nurturing environment for healing.</p>
  </section>
  <section class="abs point left p-stress">
    <h3>Stress Relief and Relaxation</h3>
    <p>Interacting with dogs has been proven to reduce<br>cortisol (stress hormone) levels and increase<br>serotonin and oxytocin, the “feel-good” hormones.<br>This natural relief from stress makes Canine Assisted<br>Therapy an ideal option for individuals dealing with<br>anxiety, trauma, PTSD, and grief,</p>
  </section>
  <section class="abs point left p-emotional-2">
    <h3>Emotional Support and Comfort</h3>
    <p>Therapy dogs provide immediate emotional support, offering<br>comfort and companionship during therapy sessions.&nbsp; Their<br>calming presence helps reduce feelings of anxiety, stress, and<br>depression, and grief, creating a safe and nurturing<br>environment for healing.</p>
  </section>

  <section class="abs point p-proven">
    <h3>Proven Effectiveness</h3>
    <p>Studies and testimonials highlight the positive effects<br>therapy dogs have on emotional, psychological and<br>physical health.</p>
  </section>
  <section class="abs point p-gentle">
    <h3>Non-Invasive and Gentle</h3>
    <p>Therapy dogs provide a natural and non-threatening<br>way to engage with patients, making it accessible for<br>individuals who may feel apprehensive about<br>traditional therapy methods.</p>
  </section>
  <section class="abs point p-safe">
    <h3>Safe and Trustworthy</h3>
    <p>All therapy dogs are carefully trained<br>to work with professionals, ensuring<br>that interactions are safe,<br>beneficial, and appropriate for<br>all individuals.</p>
  </section>

  <svg class="abs dog-photo" viewBox="0 0 182 200" role="img" aria-label="Photo of a smiling Shiba Inu in a harness offering its paw to a person's hand">
    <defs>
      <radialGradient id="dogFill" cx="0.5" cy="0.58" r="0.55">
        <stop offset="0" stop-color="#d9925a"/>
        <stop offset="0.65" stop-color="#ebc7a4"/>
        <stop offset="1" stop-color="#ffffff"/>
      </radialGradient>
    </defs>
    <rect width="182" height="200" fill="url(#dogFill)"/>
  </svg>

  <svg class="abs footer" viewBox="0 0 1200 108" aria-hidden="true">
    <defs>
      <linearGradient id="silhouette" x1="0" y1="0" x2="1" y2="1">
        <stop offset="0" stop-color="#5a1a1c"/>
        <stop offset="1" stop-color="#b4552e"/>
      </linearGradient>
    </defs>
    <rect width="1200" height="108" fill="var(--footer-grey)"/>
    <path d="M0 0 H820 C840 0 850 20 858 45 L878 108 H0 Z" fill="var(--maroon-deep)"/>
    <rect x="695" y="8" width="150" height="100" rx="40" fill="url(#silhouette)" opacity="0.7" role="img" aria-label="Silhouette illustration of a person seated with a dog"/>
    <path d="M0 0 H210 C235 0 250 25 256 60 L262 108 H0 Z" fill="var(--pink)"/>
    <circle cx="257" cy="60" r="16" fill="#fff" stroke="var(--maroon)" stroke-width="2"/>
    <path d="M249 60 H264 M258 54 L264 60 L258 66" fill="none" stroke="var(--maroon)" stroke-width="2.2" stroke-linecap="round" stroke-linejoin="round"/>
  </svg>

  <p class="abs join">Join the Healing<br>Journey Today!</p>
  <p class="abs footer-copy">Whether you are seeking emotional support or mental health<br>improvement, Canine Assisted Therapy offers a unique and compassionate<br>approach to healing.&nbsp; Connect with us today to learn more about how a<br>therapy dog can help enhance your life and well-being.</p>

  <ul class="abs contacts">
    <li>
      <svg width="24" height="24" viewBox="0 0 24 24"><circle cx="12" cy="12" r="12" fill="var(--pink)"/><path d="M8.5 6.5 l2 2.5 -1.2 1.5 c.8 1.7 2 2.9 3.7 3.7 l1.5 -1.2 2.5 2 -1.2 2 c-4.4 -.2 -8.3 -4.1 -8.5 -8.5 z" fill="#fff"/></svg>
      <span>0491 570 112</span>
    </li>
    <li>
      <svg width="24" height="24" viewBox="0 0 24 24"><circle cx="12" cy="12" r="12" fill="var(--pink)"/><rect x="6" y="8" width="12" height="8.5" fill="none" stroke="#fff" stroke-width="1.4"/><path d="M6 8 l6 5 6 -5" fill="none" stroke="#fff" stroke-width="1.4"/></svg>
      <span>hello@kindredpaws.au</span>
    </li>
    <li>
      <svg width="24" height="24" viewBox="0 0 24 24"><circle cx="12" cy="12" r="12" fill="var(--pink)"/><g fill="none" stroke="#fff" stroke-width="1.2"><circle cx="12" cy="12" r="6.5"/><ellipse cx="12" cy="12" rx="2.8" ry="6.5"/><path d="M5.5 12 h13 M6.5 9 h11 M6.5 15 h11"/></g></svg>
      <span>www.kindredpaws.au</span>
    </li>
  </ul>

</main>
</body>
</html>
```